Business card por a urban DJ, up scale audience target

Need a sober design, modern, conservative colors but i can consider some options, y play rnb, hip hop, EDM and top40.

Business card for contact and personal info, double sided, use logo attrached please; im 42 so i need a card acording to my age an target audience.

Target Market(s)

Adult people, up scale audience

Industry/Entity Type

Music Download

Contact Information for Business Card

Cel (318) 4207265518 www.lumadrift.com

Requirements
Must have
• open mind
Nice to have
• open mind
Should not have
• DJ

```html
<!DOCTYPE html>
<html lang="en">
<head>
<meta charset="utf-8">
<title>Luma – Business Card</title>
<link rel="stylesheet" href="https://fonts.googleapis.com/css2?family=Exo+2:wght@500;600&family=Arimo:wght@400&display=swap">
<style>
  :root {
    --backdrop: #3b3b3b;
    --card-dark: #2a2a2a;
    --card-light: #e6e6e6;
    --ink: #2a2a2a;
    --swoosh: #0d0d0d;
    --paper: #e6e6e6;
  }
  * { margin: 0; padding: 0; box-sizing: border-box; }
  html, body { width: 1200px; height: 750px; overflow: hidden; }
  body {
    background: var(--backdrop);
    position: relative;
    font-family: "Exo 2", sans-serif;
  }
  .card {
    position: absolute;
    width: 520px;
    height: 297px;
    top: 210px;
    overflow: hidden;
  }
  .card-front { left: 80px; background: var(--card-dark); }
  .card-back { left: 616px; background: var(--card-light); }
  .card-curves { position: absolute; left: 0; top: 0; width: 520px; height: 297px; }

  .brand-name {
    position: absolute;
    left: 0; right: 0;
    text-align: center;
    font-family: "Exo 2", sans-serif;
    font-weight: 600;
    letter-spacing: 6px;
    line-height: 1;
  }
  .card-front .brand-name { top: 72px; font-size: 96px; color: var(--paper); }
  .card-back .brand-name { top: 82px; font-size: 72px; color: var(--ink); }

  .holder {
    position: absolute;
    left: 16px;
    top: 176px;
    color: var(--ink);
  }
  .holder-name { font-size: 21px; font-weight: 500; line-height: 1.1; }
  .holder-title { font-size: 16px; font-weight: 500; line-height: 1.1; }

  .divider {
    position: absolute;
    left: 246px;
    top: 161px;
    width: 2px;
    height: 75px;
    background: var(--ink);
  }
  .contact-list {
    position: absolute;
    left: 258px;
    top: 160px;
    list-style: none;
    font-family: "Arimo", sans-serif;
    font-size: 14px;
    color: var(--ink);
  }
  .contact-item {
    display: flex;
    align-items: center;
    height: 20px;
    white-space: nowrap;
  }
  .contact-icon { width: 11px; height: 11px; margin-right: 6px; flex: none; }
</style>
</head>
<body>

<section class="card card-front" aria-label="Card front">
  <div class="brand-name">LUMA</div>
  <svg class="card-curves" viewBox="0 0 520 297" aria-hidden="true">
    <path d="M0 283 Q260 240 520 291 L520 297 L0 297 Z" fill="var(--paper)"/>
    <path d="M0 266 Q250 222 470 262 Q250 236 0 281 Z" fill="var(--swoosh)"/>
  </svg>
</section>

<section class="card card-back" aria-label="Card back">
  <div class="brand-name">LUMA</div>

  <div class="holder">
    <div class="holder-name">Daniel Whitford</div>
    <div class="holder-title">Managing Director</div>
  </div>

  <div class="divider"></div>

  <ul class="contact-list">
    <li class="contact-item">
      <svg class="contact-icon" viewBox="0 0 11 11" aria-hidden="true"><rect width="11" height="11" fill="var(--ink)"/><path d="M2.5 3.5 Q5.5 1.5 8.5 3.5 L7.5 4.5 L6.5 4 L4.5 4 L3.5 4.5 Z M3 6 H8 V8.5 H3 Z" fill="var(--paper)"/></svg>
      (318) 4207265518
    </li>
    <li class="contact-item">
      <svg class="contact-icon" viewBox="0 0 11 11" aria-hidden="true"><rect width="11" height="11" fill="var(--ink)"/><rect x="2.5" y="3.5" width="6" height="4" fill="var(--paper)"/><path d="M2.5 3.5 L5.5 6 L8.5 3.5" stroke="var(--ink)" stroke-width="0.8" fill="none"/></svg>
      info@lumadrift.com
    </li>
    <li class="contact-item">
      <svg class="contact-icon" viewBox="0 0 11 11" aria-hidden="true"><rect width="11" height="11" fill="var(--ink)"/><circle cx="5.5" cy="5.5" r="3" fill="none" stroke="var(--paper)" stroke-width="1"/><path d="M2.5 5.5 H8.5 M5.5 2.5 V8.5" stroke="var(--paper)" stroke-width="0.7"/></svg>
      www.lumadrift.com
    </li>
    <li class="contact-item">
      <svg class="contact-icon" viewBox="0 0 11 11" aria-hidden="true"><rect width="11" height="11" fill="var(--ink)"/><path d="M5.5 9 L3.3 5.3 A2.4 2.4 0 1 1 7.7 5.3 Z" fill="var(--paper)"/><circle cx="5.5" cy="4.3" r="0.9" fill="var(--ink)"/></svg>
      418 Harbor View Rd, Calder MD 214
    </li>
  </ul>

  <svg class="card-curves" viewBox="0 0 520 297" aria-hidden="true">
    <path d="M0 297 L0 290 Q260 244 520 284 L520 297 Z" fill="var(--card-dark)"/>
    <path d="M50 270 Q300 236 520 262 L520 284 Q300 250 50 270 Z" fill="var(--swoosh)"/>
  </svg>
</section>

</body>
</html>
```